New business card/stationary for a consulting company

I am looking for a clean and very professional looking business card for my consulting company as well as corresponding stationary. I am uploading our logo. I like simple and powerful for the feel. No graphics but I am open on everything else. Below is my contact information but would like the final to be in a version I can add my employees information into and print. Thank you.

Daniel Whitcombe
dan@ferncliffadvisory.com
2870 North 9th Avenue, Summit Floor, Elm Ridge, Illinois 60531
www.ferncliffadvisory.com

Industry/Entity Type

Consulting

Contact Information for Business Card

Daniel Whitcombe
dan@ferncliffadvisory.com
www.ferncliffadvisory.com

Font styles to use
Serif
Sans Serif

Requirements
Must have
• Our logo and the business card details.
Nice to have
• our website www.ferncliffadvisory.com

```html
<!DOCTYPE html>
<html lang="en">
<head>
<meta charset="utf-8">
<title>Ferncliff Advisory – Business Card</title>
<link href="https://fonts.googleapis.com/css2?family=Marcellus&family=Roboto:wght@400&display=swap" rel="stylesheet">
<style>
  :root {
    --backdrop: #d8d3cb;
    --card: #f3f4f6;
    --navy: #1c2f5e;
    --navy-soft: rgba(28, 47, 94, 0);
    --ink: #1f2a4a;
    --text: #2a2a2e;
    --tan: #e2d8c6;
  }
  html, body {
    margin: 0;
    width: 1200px;
    height: 970px;
    overflow: hidden;
    background: var(--backdrop);
  }
  .card {
    position: absolute;
    left: 100px;
    top: 207px;
    width: 1000px;
    height: 556px;
    background: var(--card);
    border-radius: 4px;
    box-shadow: 0 10px 30px rgba(0, 0, 0, 0.18);
    overflow: hidden;
  }
  .card-decoration {
    position: absolute;
    left: 0;
    right: 0;
    bottom: 0;
    height: 300px;
    background: linear-gradient(172deg, var(--navy-soft) 8%, rgba(28, 47, 94, 0.55) 38%, var(--navy) 62%);
  }
  .brand-mark {
    position: absolute;
    left: 225px;
    top: 100px;
    width: 84px;
    height: 84px;
    background: var(--navy);
  }
  .brand-name {
    position: absolute;
    left: 67px;
    top: 222px;
    width: 400px;
    margin: 0;
    text-align: center;
    font-family: "Marcellus", serif;
    font-weight: 400;
    font-size: 47px;
    line-height: 61px;
    letter-spacing: 2px;
    color: var(--ink);
    text-transform: uppercase;
  }
  .holder {
    position: absolute;
    right: 43px;
    top: 76px;
    text-align: right;
  }
  .holder-name {
    margin: 0 0 14px;
    font-family: "Marcellus", serif;
    font-size: 33px;
    letter-spacing: 2px;
    color: var(--ink);
    text-transform: uppercase;
    font-weight: 400;
  }
  .holder-address {
    margin: 0;
    font-family: "Roboto", sans-serif;
    font-size: 23px;
    line-height: 37px;
    color: var(--text);
    font-style: normal;
  }
  .contact-list {
    position: absolute;
    right: 43px;
    top: 430px;
    margin: 0;
    padding: 0;
    list-style: none;
    font-family: "Roboto", sans-serif;
    font-size: 23px;
    line-height: 37px;
    color: var(--tan);
    text-align: right;
  }
  .contact-list li {
    display: flex;
    justify-content: flex-end;
    align-items: center;
    gap: 8px;
  }
  .contact-icon {
    width: 20px;
    height: 20px;
    flex: none;
  }
</style>
</head>
<body>
  <div class="card">
    <div class="card-decoration" role="img" aria-label="Navy and charcoal wave decoration across the lower card"></div>

    <div class="brand-mark"></div>
    <h1 class="brand-name">Ferncliff<br>Advisory</h1>

    <div class="holder">
      <h2 class="holder-name">Daniel Whitcombe</h2>
      <address class="holder-address">2870 North 9th Avenue, Summit<br>Floor, Elm Ridge, Illinois 60531</address>
    </div>

    <ul class="contact-list">
      <li>ferncliffadvisory.com
        <svg class="contact-icon" viewBox="0 0 20 20" aria-hidden="true">
          <g fill="none" stroke="var(--tan)" stroke-width="1.4">
            <circle cx="10" cy="10" r="8"/>
            <ellipse cx="10" cy="10" rx="3.5" ry="8"/>
            <line x1="2" y1="10" x2="18" y2="10"/>
          </g>
        </svg>
      </li>
      <li>dan@ferncliffadvisory.com
        <svg class="contact-icon" viewBox="0 0 20 20" aria-hidden="true">
          <rect x="1" y="4" width="18" height="12" fill="var(--tan)"/>
          <path d="M1,4 L10,11 L19,4" fill="none" stroke="var(--navy)" stroke-width="1.3"/>
        </svg>
      </li>
    </ul>
  </div>
</body>
</html>
```